Accountability Project Graphics

I want to create 10 social media graphics (new Instagram size 4:5 (1080 x 1350 pixels) focusing on our Quilvo Accountability App, using any of the 3 pictures attached. Use the attached pics only, NO RANDOM STOCK PHOTOGRAPHY. For the color scheme, use the landing page colors/fonts (attached).
You can add any of the 3 photos attached but I mainly need BOLD text that includes these headlines and sub-headlines on them.
Please NOTE for all the headlines below, also add this sub-headline on each graphic:
Stay Consistent with RT in Your Pocket!
Here are the headlines:
• Stop Starting Over Every Monday
• You don't need more willpower. You need more support
• Built for women who are tired of doing this alone
• When Motivation Fades, RT Checks In
• The Support System You've Been Missing
• Support When Motivation Disappears
• What if RT Checked in Every Day?
• The Missing Piece Isn't Another Diet
• Eat the food you love. Stay accountable every day.
• One Bad Meal Doesn't Mean You Failed
women over 40 trying to lose weight

```html
<!DOCTYPE html>
<html lang="en">
<head>
<meta charset="utf-8">
<title>Accountability App Social Graphics</title>
<link rel="stylesheet" href="https://fonts.googleapis.com/css2?family=Playfair+Display:ital,wght@0,800;0,900;1,800;1,900&family=Permanent+Marker&family=Oswald:wght@500;600&family=Josefin+Sans:wght@300&family=Rubik:ital,wght@0,900;1,900&family=Open+Sans:wght@500;600&display=block">
<style>
  :root {
    --canvas: #e9e4e7;
    --blush-light: #f2d3e1;
    --blush: #eab7cd;
    --plum-deep: #230817;
    --plum: #5a0f35;
    --magenta: #b0105a;
    --accent: #e0177d;
    --wine: #7d0f43;
    --ink: #111111;
    --white: #ffffff;
    --frame-light: #d98cb0;
    --frame-dark: rgba(255,255,255,0.45);
  }
  * { margin: 0; padding: 0; box-sizing: border-box; }
  html, body { width: 1200px; height: 297px; overflow: hidden; background: var(--canvas); }
  .strip { position: relative; width: 1200px; height: 297px; }
  .post { position: absolute; top: 6px; width: 228px; height: 285px; overflow: hidden; }
  .post--light { background: linear-gradient(160deg, var(--blush-light), var(--blush)); }
  .post--dark { background: linear-gradient(120deg, var(--plum-deep) 10%, var(--plum) 45%, var(--magenta) 100%); }
  .post__frame { position: absolute; inset: 4px; border: 1px solid var(--frame-light); z-index: 3; pointer-events: none; }
  .post--dark .post__frame { border-color: var(--frame-dark); }
  .photo { position: absolute; z-index: 1; border-radius: 40px 40px 0 0; }
  .line { position: absolute; left: 12px; white-space: nowrap; line-height: 1; z-index: 2; transform-origin: left center; }
  .serif { font-family: "Playfair Display", Georgia, serif; font-weight: 900; }
  .brush { font-family: "Permanent Marker", "Comic Sans MS", cursive; font-weight: 400; }
  .condensed { font-family: "Oswald", "Arial Narrow", sans-serif; font-weight: 600; text-transform: uppercase; }
  .thin { font-family: "Josefin Sans", sans-serif; font-weight: 300; }
  .heavy { font-family: "Rubik", sans-serif; font-weight: 900; }
  .plain { font-family: "Open Sans", Arial, sans-serif; font-weight: 500; }
  .tagline {
    position: absolute; left: 12px; z-index: 2; font-family: "Open Sans", Arial, sans-serif;
    font-weight: 500; font-size: 8.6px; line-height: 13px; color: var(--ink);
  }
  .post--dark .tagline { color: var(--white); font-weight: 600; }
  .tagline .name { color: var(--accent); }
  .ink { color: var(--ink); }
  .white { color: var(--white); }
  .accent { color: var(--accent); }
  .wine { color: var(--wine); }
</style>
</head>
<body>
<main class="strip">

  <section class="post post--light" style="left:5px">
    <div class="photo" role="img" aria-label="Two women sharing a joyful hug" style="left:100px;top:107px;width:128px;height:178px;background:linear-gradient(160deg,#3a2a30,#e8417f 55%,#e7f0b8)"></div>
    <div class="post__frame"></div>
    <p class="line serif ink" style="top:23px;font-size:19px">YOU DON’T</p>
    <p class="line serif ink" style="top:49px;font-size:19px">NEED <span class="wine">MORE</span></p>
    <p class="line serif wine" style="top:78px;font-size:19px">WILLPOWER</p>
    <p class="line serif ink" style="top:108px;font-size:19px">YOU</p>
    <p class="line serif ink" style="top:133px;font-size:19px">NEED</p>
    <p class="line serif ink" style="top:158px;font-size:19px">MORE</p>
    <p class="line brush wine" style="top:188px;font-size:24px;transform:scaleX(0.7)">SUPPORT</p>
    <p class="tagline" style="top:220px">Stay Consistent<br>with <span class="name">RT</span> in Your<br>Pocket!</p>
  </section>

  <section class="post post--dark" style="left:248px">
    <div class="photo" role="img" aria-label="Two women laughing together in denim outfits" style="left:80px;top:104px;width:148px;height:181px;background:linear-gradient(180deg,#2b2438,#34476a 50%,#1c2a44)"></div>
    <div class="post__frame"></div>
    <p class="line condensed white" style="top:16px;font-size:27px">BUILT FOR</p>
    <p class="line brush accent" style="top:50px;font-size:32px;transform:skewX(-10deg) scaleX(0.85)">WOMEN</p>
    <p class="line condensed white" style="top:92px;font-size:22px">WHO ARE</p>
    <p class="line condensed white" style="top:119px;font-size:22px">TIRED OF</p>
    <p class="line condensed white" style="top:146px;font-size:22px">DOING</p>
    <p class="line condensed white" style="top:173px;font-size:22px">THIS</p>
    <p class="line brush accent" style="top:199px;font-size:23px;transform:skewX(-10deg) scaleX(0.8)">ALONE</p>
    <p class="tagline" style="top:234px">Stay Consistent<br>with <span class="name">RT</span> in Your<br>Pocket!</p>
  </section>

  <section class="post post--light" style="left:490px">
    <div class="photo" role="img" aria-label="Smiling coach in a black lace outfit posing" style="left:113px;top:61px;width:112px;height:224px;background:linear-gradient(180deg,#2a1a1e,#111 40%,#1b1b1b)"></div>
    <div class="post__frame"></div>
    <p class="line thin ink" style="top:35px;font-size:23px">WHEN</p>
    <p class="line heavy wine" style="top:69px;font-size:18px">MOTIVATION</p>
    <p class="line thin ink" style="top:100px;font-size:23px">FADES</p>
    <p class="line heavy wine" style="top:131px;font-size:21px;font-style:italic">RT</p>
    <p class="line heavy wine" style="top:162px;font-size:21px;font-style:italic">CHECKS</p>
    <p class="line heavy wine" style="top:194px;font-size:21px;font-style:italic">IN</p>
    <p class="tagline" style="top:226px;font-weight:600">Stay Consistent<br>with <span class="name">RT</span> in Your Pocket!</p>
  </section>

  <section class="post post--dark" style="left:726px">
    <div class="photo" role="img" aria-label="Smiling coach in a black lace outfit posing" style="left:100px;top:47px;width:126px;height:238px;background:linear-gradient(180deg,#1e0c16,#0d0a0c 40%,#141014)"></div>
    <div class="post__frame"></div>
    <p class="line serif white" style="top:22px;font-size:19px">WHAT IF</p>
    <p class="line serif accent" style="top:50px;font-size:40px">RT</p>
    <p class="line serif white" style="top:103px;font-size:19px">CHECKED</p>
    <p class="line serif white" style="top:132px;font-size:19px">IN</p>
    <p class="line serif accent" style="top:161px;font-size:23px;font-style:italic">EVERY</p>
    <p class="line serif accent" style="top:193px;font-size:23px;font-style:italic">DAY?</p>
    <p class="tagline" style="top:228px">Stay Consistent<br>with <span class="name">RT</span> in Your<br>Pocket!</p>
  </section>

  <section class="post post--light" style="left:967px">
    <div class="photo" role="img" aria-label="Two women sharing a joyful hug" style="left:86px;top:100px;width:142px;height:185px;background:linear-gradient(160deg,#3a2a30,#e8417f 55%,#e7f0b8)"></div>
    <div class="post__frame"></div>
    <p class="line plain ink" style="top:22px;font-size:19px">THE</p>
    <p class="line brush wine" style="top:50px;font-size:28px;transform:scaleX(0.7)">SUPPORT</p>
    <p class="line brush wine" style="top:89px;font-size:28px;transform:scaleX(0.7)">SYSTEM</p>
    <p class="line plain ink" style="top:132px;font-size:15px">YOU'VE</p>
    <p class="line plain ink" style="top:156px;font-size:15px">BEEN</p>
    <p class="line plain wine" style="top:181px;font-size:16px">MISSING</p>
    <p class="tagline" style="top:209px">Stay Consistent<br>with <span class="name">RT</span> in Your<br>Pocket!</p>
  </section>

</main>
</body>
</html>
```